Tolbek cards

I want a simple business card that pops.
Logo on one side.
On side two i want.
"Are you thinking about a new building on your property, or renovating an existing structure? Contact".....
Owners Name: Dale Whitacre
Owners Phone number: 610-555-0187
Address:4076 Copper Ridge RD, Millbrook, PA 17345
Committed to Quality, Service, and Integrity

```html
<!DOCTYPE html>
<html lang="en">
<head>
<meta charset="utf-8">
<title>Tolbek Builders – Business Cards</title>
<link rel="stylesheet" href="https://fonts.googleapis.com/css2?family=Bebas+Neue&family=Montserrat:wght@400;600;800&family=Poppins:wght@400&display=swap">
<style>
  :root {
    --backdrop: #1c1c1c;
    --brown: #3f2c1e;
    --brown-soft: #8c7259;
    --ink: #2b2b2b;
    --white: #ffffff;
  }
  * { margin: 0; padding: 0; box-sizing: border-box; }
  html, body {
    width: 1200px; height: 1015px; overflow: hidden;
    background: var(--backdrop);
  }
  .stage {
    position: relative; width: 1200px; height: 1015px;
    display: flex; flex-direction: column; align-items: center; justify-content: center; gap: 50px;
  }
  .card {
    width: 580px; height: 331px; position: relative; overflow: hidden;
    box-shadow: 0 10px 30px rgba(0,0,0,.5);
  }

  /* Front */
  .card-front {
    background: var(--brown);
    display: flex; align-items: center; justify-content: center; gap: 14px;
  }
  .brand-square { width: 26px; height: 26px; background: var(--white); flex: none; }
  .brand-name {
    font-family: "Montserrat", sans-serif; font-weight: 800;
    font-size: 32px; color: var(--white); letter-spacing: 1px; line-height: 1;
    white-space: nowrap;
  }

  /* Back */
  .card-back { background: var(--white); }
  .headline-band {
    position: absolute; left: 0; top: 0; width: 100%; height: 185px;
    background: var(--brown);
    padding: 78px 150px 0 28px;
  }
  .headline {
    font-family: "Bebas Neue", sans-serif; color: var(--white);
    font-size: 27px; line-height: 1.02; letter-spacing: .4px;
  }
  .contact {
    position: absolute; left: 40px; top: 206px;
    font-family: "Poppins", sans-serif; color: var(--ink);
  }
  .contact-label { font-size: 14px; }
  .contact-name {
    font-family: "Montserrat", sans-serif; font-weight: 600;
    font-size: 21px; color: var(--brown-soft); letter-spacing: .5px; margin: 0 0 6px;
  }
  .contact-row { display: flex; align-items: flex-start; gap: 10px; font-size: 14px; line-height: 1.25; margin-top: 4px; }
  .contact-row svg { flex: none; margin-top: 1px; }
  .tagline {
    position: absolute; right: 30px; top: 238px; text-align: right;
    font-family: "Bebas Neue", sans-serif; color: var(--brown);
    font-size: 25px; line-height: 1;
  }
</style>
</head>
<body>
<main class="stage">
  <section class="card card-front" aria-label="Card front">
    <span class="brand-square"></span>
    <span class="brand-name">TOLBEK BUILDERS LLC</span>
  </section>

  <section class="card card-back" aria-label="Card back">
    <div class="headline-band">
      <p class="headline">Are you thinking about a new building on your property, or renovating an existing structure?</p>
    </div>

    <div class="contact">
      <p class="contact-label">Contact</p>
      <p class="contact-name">DALE WHITACRE</p>
      <div class="contact-row">
        <svg width="18" height="18" viewBox="0 0 18 18" aria-hidden="true">
          <circle cx="9" cy="9" r="9" fill="var(--brown)"/>
          <path d="M6.2 4.8l1.4 1.6-.7 1.1c.5 1.2 1.4 2.1 2.6 2.6l1.1-.7 1.6 1.4-.8 1.4c-3.3-.3-5.8-2.8-6.1-6.1z" fill="var(--white)"/>
        </svg>
        <span>610-555-0187</span>
      </div>
      <div class="contact-row">
        <svg width="18" height="18" viewBox="0 0 18 18" aria-hidden="true">
          <circle cx="9" cy="9" r="9" fill="var(--brown)"/>
          <path d="M9 4.3a3 3 0 0 0-3 3c0 2.2 3 6 3 6s3-3.8 3-6a3 3 0 0 0-3-3zm0 4.1a1.1 1.1 0 1 1 0-2.2 1.1 1.1 0 0 1 0 2.2z" fill="var(--white)"/>
        </svg>
        <span>4076 Copper Ridge RD,<br>Millbrook, PA 17345</span>
      </div>
    </div>

    <p class="tagline">Committed to quality,<br>service and integrity</p>
  </section>
</main>
</body>
</html>
```